Lumbra Ember Oven Kitchen (restaurant)

Restaurant with a cool vibe.
We need a refresh of existing site. Appealing to a hip crowd of 25 or older age bracket (mid price to high small town). Constant changes food and cocktail menu. A vibing atmosphere with jazz funk hip music.
Must be able to scale for any device… phone/mobile device super important.
Instagram: @Lumbra.Bexwell
Website: lumbrabexwell.example

Target Market(s)

25-55 age group

Number of Pages Required

1 page

Font styles to use
Sans Serif

Requirements
Must have
• Simple to navigate. Simplicity is the key to all sophistication.

Links/Buttons
Menu
Gift Cards
Reservations
Take Out
Contact Us
Should not have
• Please, nothing generic looking… no cookie cutter look. Originality

```html
<!DOCTYPE html>
<html lang="en">
<head>
<meta charset="utf-8">
<title>Lumbra Ember Oven Kitchen</title>
<link rel="stylesheet" href="https://fonts.googleapis.com/css2?family=Poppins:wght@500;600;700;800&family=Roboto:wght@400;500&family=Allura&display=swap">
<style>
:root{
  --tan:#c4a588;
  --tan-soft:#d9c2a9;
  --ink:#111;
  --text:#555;
  --white:#fff;
  --night:#1e1a18;
  --hero-a:#5b5a4a;
  --hero-b:#3a3c33;
}
*{margin:0;padding:0;box-sizing:border-box}
html,body{width:1200px;height:3153px;overflow:hidden}
body{position:relative;font-family:Roboto,Arial,sans-serif;background:var(--white);color:var(--text)}
.abs{position:absolute}
.btn{position:absolute;display:flex;align-items:center;justify-content:center;font-family:Poppins,sans-serif;font-weight:700;font-size:15px;color:var(--white);background:var(--tan);text-transform:uppercase}
.btn-outline{background:transparent;border:2px solid var(--white)}
.btn-dark{background:#000}
/* hero */
.hero{left:0;top:0;width:1200px;height:642px;background:radial-gradient(circle at 25% 40%,#6e7042 0,transparent 35%),radial-gradient(circle at 70% 20%,#8a5a32 0,transparent 30%),linear-gradient(135deg,var(--hero-a),var(--hero-b))}
.hero::after{content:"";position:absolute;inset:0;background:rgba(0,0,0,.28)}
.brand{left:111px;top:16px;font-family:Poppins,sans-serif;font-weight:800;font-size:24px;line-height:34px;color:var(--white);z-index:2;text-transform:uppercase}
.nav{left:459px;top:0;z-index:2;display:flex;font-family:Poppins,sans-serif;font-weight:600;font-size:13.5px;color:var(--white)}
.nav a{color:inherit;text-decoration:none;height:90px;display:flex;align-items:center;padding:0 9px;margin-right:22px}
.nav a.active{background:var(--tan);margin-right:14px}
.nav-rule{left:111px;top:92px;width:978px;height:3px;border-top:1px solid rgba(255,255,255,.7);border-bottom:1px solid rgba(255,255,255,.5);z-index:2}
.hero-title{left:0;top:270px;width:1200px;text-align:center;font-family:Poppins,sans-serif;font-weight:800;font-size:42px;color:var(--white);z-index:2}
.slide-arrow{width:38px;height:38px;border-radius:50%;background:#111;z-index:2;display:flex;align-items:center;justify-content:center}
.down{left:575px;top:617px;width:50px;height:50px;background:var(--tan);z-index:2;display:flex;align-items:center;justify-content:center}
.plate{left:815px;top:565px;width:275px;height:155px;border-radius:50%;background:radial-gradient(ellipse at 50% 40%,#c46a35 0,#b98a5a 40%,#f2f0ec 62%,#dcdad6 100%);z-index:3}
/* restaurant */
.h2{font-family:Poppins,sans-serif;font-weight:800;color:var(--ink);text-transform:uppercase}
.about p{font-size:13.5px;line-height:22.3px;margin-bottom:22px}
.photo{background:linear-gradient(135deg,#7a5a3c,#c9a27a 50%,#6b4a30)}
.thumb{top:1154px;width:216px;height:177px;display:flex;align-items:flex-end;justify-content:center;padding-bottom:22px;font-family:Poppins,sans-serif;font-size:16px;color:var(--white)}
.play{left:813px;top:1011px;width:80px;height:80px;border-radius:50%;border:3px solid var(--white)}
/* menu band */
.menuband{left:0;top:1434px;width:1200px;height:448px;background:radial-gradient(circle at 60% 40%,#6a5f55 0,transparent 45%),linear-gradient(120deg,#3f3b37,#2a2826 60%,#4a4440)}
.script{font-family:Allura,cursive;color:var(--tan);}
/* reservations */
.wood{left:0;top:1882px;width:1200px;height:623px;background:linear-gradient(180deg,var(--tan-soft),#cfb496)}
.card{left:662px;top:1966px;width:420px;height:262px;background:var(--white);border-radius:14px;box-shadow:0 6px 20px rgba(0,0,0,.2)}
.card-back{left:645px;top:1945px;width:450px;height:310px;background:linear-gradient(135deg,#c79a2a,#8a6420);border-radius:14px;transform:rotate(3deg)}
.footer{left:0;top:2505px;width:1200px;height:648px;background:var(--night)}
.map{left:109px;top:2292px;width:982px;height:432px;border:2px solid var(--white);background:linear-gradient(135deg,#eef0ee,#e3e7e4 60%,#d7e3ea)}
.icon{width:80px;height:80px;border-radius:50%;border:2px solid var(--tan);display:flex;align-items:center;justify-content:center}
.icon span{width:58px;height:58px;border-radius:50%;border:1px solid var(--tan);display:flex;align-items:center;justify-content:center}
.contact{width:330px;text-align:center;color:var(--white);font-size:20px;line-height:27px;top:2860px}
.hours{left:0;width:1200px;text-align:center;color:var(--white);font-size:14px}
.hours b{font-family:Poppins,sans-serif;font-weight:600;color:var(--tan);font-size:18px;margin-right:24px}
.social{width:36px;height:36px;border-radius:50%;border:1px solid #bbb;top:3077px}
</style>
</head>
<body>
<section class="abs hero" role="img" aria-label="Overhead photo of bowls of dips on a woven cloth"></section>
<div class="abs brand">Lumbra Ember<br>Oven Kitchen</div>
<nav class="abs nav"><a class="active">HOME</a><a>GIFT CARDS</a><a>MENU</a><a>CONTACT US</a><a>RESERVATIONS</a><a style="margin-right:0">TAKE OUT</a></nav>
<div class="abs nav-rule"></div>
<h1 class="abs hero-title">LETS GET LUNCH AT LUMBRA!</h1>
<div class="btn" style="left:441px;top:343px;width:152px;height:49px;z-index:2">Book a Table</div>
<div class="btn btn-outline" style="left:607px;top:343px;width:151px;height:49px;z-index:2">Order Online</div>
<div class="abs slide-arrow" style="left:36px;top:344px"><svg width="12" height="12" viewBox="0 0 12 12"><path d="M8 1 3 6l5 5" fill="none" stroke="#fff" stroke-width="2"/></svg></div>
<div class="abs slide-arrow" style="left:1129px;top:344px"><svg width="12" height="12" viewBox="0 0 12 12"><path d="M4 1l5 5-5 5" fill="none" stroke="#fff" stroke-width="2"/></svg></div>
<div class="abs down"><svg width="14" height="16" viewBox="0 0 14 16"><path d="M7 1v12M2 8l5 6 5-6" fill="none" stroke="#fff" stroke-width="2.5"/></svg></div>
<div class="abs plate" role="img" aria-label="Grilled chicken sandwich on a white plate"></div>

<section class="about">
  <h2 class="abs h2" style="left:111px;top:762px;font-size:34px">Restaurant</h2>
  <div class="abs" style="left:111px;top:818px;width:480px">
    <p>Lorem ipsum dolor sit amet, consectetur adipiscing elit, sed do eiusmod tempor incididunt ut labore et dolore magna aliqua. Ut enim ad minim veniam, quis nostrud exercitation ullamco laboris nisi ut aliquip ex ea commodo consequat. Duis aute irure dolor in reprehenderit in voluptate velit esse cillum dolore eu fugiat nulla pariatur. Excepteur sint occaecat cupidatat non proident, sunt in culpa qui officia deserunt mollit anim id est laborum.</p>
    <p>Lorem ipsum dolor sit amet, consectetur adipiscing elit, sed do eiusmod tempor incididunt ut labore et dolore magna aliqua. Ut enim ad minim veniam, quis nostrud exercitation ullamco laboris nisi ut aliquip ex ea commodo consequat. Duis aute irure dolor</p>
  </div>
  <div class="btn" style="left:112px;top:1083px;width:151px;height:50px">Book a Table</div>
  <div class="abs photo" style="left:619px;top:770px;width:470px;height:561px" role="img" aria-label="Wood fired pizzas on a table"></div>
  <div class="abs play"><svg width="74" height="74" viewBox="0 0 74 74"><path d="M30 24v26l21-13z" fill="none" stroke="#fff" stroke-width="3"/></svg></div>
  <div class="abs thumb" style="left:112px;background:linear-gradient(135deg,#6a4b2e,#a8803e,#5a6b2e)" role="img" aria-label="Burger with avocado">Lorem ipsum dolor</div>
  <div class="abs thumb" style="left:346px;background:linear-gradient(135deg,#5a2f22,#8a4a35,#4a5a2a)" role="img" aria-label="Salad with greens">Lorem ipsum dolor</div>
  <div class="abs thumb" style="left:579px;background:linear-gradient(135deg,#5a3a5c,#7a6a3a,#3a4a2a)" role="img" aria-label="Wrap with red cabbage">Lorem ipsum dolor</div>
  <svg class="abs" style="left:36px;top:1235px" width="40" height="16" viewBox="0 0 40 16"><path d="M9 2 3 8l6 6" fill="none" stroke="#333" stroke-width="1.5"/><path d="M30 2l6 6-6 6" fill="none" stroke="#c4a588" stroke-width="1.5"/></svg>
</section>

<section class="abs menuband" role="img" aria-label="Close-up of a plated dish"></section>
<div class="abs script" style="left:95px;top:1520px;font-size:110px;line-height:1;opacity:.9">Menu</div>
<h2 class="abs" style="left:111px;top:1625px;font-family:Poppins,sans-serif;font-weight:700;font-size:34px;color:#fff">LUMBRA EMBER OVEN KITCHEN</h2>
<div class="btn" style="left:112px;top:1690px;width:151px;height:49px">Dinner</div>
<div class="btn" style="left:270px;top:1690px;width:151px;height:49px">Takeout</div>

<section class="abs wood"></section>
<div class="abs script" style="left:110px;top:1940px;font-size:50px;color:#2a2622">Lumbra Ember Oven Kitchen</div>
<h2 class="abs" style="left:110px;top:2015px;font-family:Poppins,sans-serif;font-weight:800;font-size:35px;line-height:44px;color:#fff">RESERVATIONS ARE NOT<br>CURRENTLY AVAILABLE</h2>
<p class="abs" style="left:111px;top:2110px;width:440px;font-size:13.5px;line-height:26px;color:#fff">Reservations will not be available for the courtyard under phase 1 and 2 of reopening. Walk-ins only. We can't wait to see you!</p>
<div class="btn btn-dark" style="left:111px;top:2180px;width:152px;height:50px">Book Now</div>
<div class="abs card-back"></div>
<div class="abs card">
  <div class="abs" style="left:16px;top:55px;width:250px;height:190px;border-radius:50%;background:radial-gradient(ellipse,#b8742e 0,#d9a45a 45%,#fff 72%)" role="img" aria-label="Crispy chicken burger"></div>
  <div class="abs" style="left:285px;top:80px;font-family:Poppins,sans-serif;font-weight:800;font-size:34px;line-height:43px;color:#111">GIFT<br><span style="color:var(--tan)">CARD</span></div>
</div>

<section class="abs footer" role="img" aria-label="Dim evening view of the restaurant storefront"></section>
<div class="abs map" role="img" aria-label="Street map showing the restaurant location by the river"></div>

<div class="abs icon" style="left:233px;top:2765px"><span><svg width="16" height="20" viewBox="0 0 16 20"><path d="M8 1a6 6 0 0 0-6 6c0 5 6 12 6 12s6-7 6-12a6 6 0 0 0-6-6z" fill="#fff"/><circle cx="8" cy="7" r="2.2" fill="#1e1a18"/></svg></span></div>
<div class="abs icon" style="left:560px;top:2765px"><span><svg width="18" height="18" viewBox="0 0 18 18"><path d="M4 1l3 4-2 2c1 3 3 5 6 6l2-2 4 3-2 3C8 17 1 10 1 3z" fill="#fff"/></svg></span></div>
<div class="abs icon" style="left:885px;top:2765px"><span><svg width="20" height="14" viewBox="0 0 20 14"><rect width="20" height="14" rx="1" fill="#fff"/><path d="M1 1l9 7 9-7" fill="none" stroke="#1e1a18" stroke-width="1.5"/></svg></span></div>
<div class="abs contact" style="left:108px">48 Harrow Lane<br>Bexwell, ON</div>
<div class="abs contact" style="left:435px">Phone:<br>555-014-0288</div>
<div class="abs contact" style="left:760px">Email :<br>hello@lumbrabexwell.example</div>
<div class="abs hours" style="top:2950px"><b>Dining Hours :</b>Courtyard is open &nbsp;|&nbsp; Thursday to Sunday &nbsp;|&nbsp; 12:00pm – 9:00pm</div>
<div class="abs hours" style="top:2993px"><b style="margin-right:14px">Pickup &amp; Kitchen Hours :</b>Thursday to Sunday &nbsp;|&nbsp; 12:00pm – 8:00pm</div>
<div class="abs" style="left:111px;top:3054px;width:978px;height:1px;background:var(--tan)"></div>
<div class="abs" style="left:111px;top:3087px;font-size:14px;color:#fff">© Copyrights 2021 Company Name &nbsp;| &nbsp; All Rights Reserved</div>
<div class="abs social" style="left:930px"></div>
<div class="abs social" style="left:972px"></div>
<div class="abs social" style="left:1012px"></div>
<div class="abs social" style="left:1053px"></div>
</body>
</html>
```